Business card design for my company.
I would like the card's background colour to be black. You can also see our web site to get an idea of our brand. https://www.tmwhomecrafting.com.au/
- Name
- Email

```html
<!DOCTYPE html>
<html lang="en">
<head>
<meta charset="utf-8">
<title>TMW Home Crafting – Business Card</title>
<link href="https://fonts.googleapis.com/css2?family=Roboto:wght@400;500;700&display=swap" rel="stylesheet">
<style>
  :root {
    --page: #f3f3f3;
    --brand-green: #13964a;
    --card-dark: #1f1f1f;
    --white: #ffffff;
    --swoosh: #f4f5f8;
  }
  * { margin: 0; padding: 0; box-sizing: border-box; }
  html, body { width: 1200px; height: 987px; overflow: hidden; }
  body {
    background: var(--page);
    font-family: "Roboto", sans-serif;
    position: relative;
  }
  .card {
    position: absolute;
    left: 245px;
    width: 710px;
    height: 406px;
    overflow: hidden;
  }
  .card-front { top: 68px; background: var(--brand-green); }
  .card-back { top: 514px; background: var(--card-dark); }

  .wordmark {
    position: absolute;
    left: 0; right: 0;
    text-align: center;
    font-weight: 700;
    letter-spacing: 3px;
    color: var(--white);
  }
  .card-front .wordmark { top: 160px; font-size: 44px; }
  .card-back .wordmark { top: 66px; font-size: 40px; }

  .front-web {
    position: absolute;
    left: 0; right: 0;
    top: 356px;
    text-align: center;
    font-size: 17px;
    letter-spacing: 0.6px;
    color: var(--white);
  }

  .person {
    position: absolute;
    right: 391px;
    top: 218px;
    text-align: right;
    color: var(--white);
  }
  .person-name { font-size: 34px; font-weight: 400; line-height: 1.1; }
  .person-name .first { color: var(--brand-green); font-weight: 700; }
  .person-title { font-size: 17px; letter-spacing: 0.5px; }

  .divider {
    position: absolute;
    left: 353px;
    top: 204px;
    width: 2px;
    height: 89px;
    background: var(--brand-green);
  }

  .contacts {
    position: absolute;
    left: 389px;
    top: 214px;
    list-style: none;
    color: var(--white);
    font-size: 17.5px;
    letter-spacing: 0.4px;
  }
  .contacts li { display: flex; align-items: center; height: 23px; }
  .contacts svg { width: 16px; height: 16px; margin-right: 11px; fill: var(--brand-green); }
  .contacts .accent { color: var(--brand-green); }

  .footer-band { position: absolute; left: 0; top: 0; width: 710px; height: 406px; }

  .location {
    position: absolute;
    left: 0; right: 0;
    top: 355px;
    text-align: center;
    font-size: 17px;
    letter-spacing: 0.5px;
    color: var(--white);
  }
</style>
</head>
<body>

<section class="card card-front">
  <div class="wordmark">TMW HOME CRAFTING</div>
  <p class="front-web">www.tmwhomecrafting.com.au</p>
</section>

<section class="card card-back">
  <svg class="footer-band" viewBox="0 0 710 406" aria-hidden="true">
    <path d="M0 286 Q355 420 710 286 L710 406 L0 406 Z" fill="var(--brand-green)"/>
    <path d="M27 287 Q355 392 684 287 Q355 378 27 287 Z" fill="var(--swoosh)"/>
  </svg>

  <div class="wordmark">TMW HOME CRAFTING</div>

  <div class="person">
    <p class="person-name"><span class="first">Liam</span> Harcourt</p>
    <p class="person-title">General Manager</p>
  </div>

  <div class="divider"></div>

  <ul class="contacts">
    <li>
      <svg viewBox="0 0 24 24"><path d="M6.6 10.8a15.1 15.1 0 0 0 6.6 6.6l2.2-2.2a1 1 0 0 1 1-.25 11.4 11.4 0 0 0 3.6.57 1 1 0 0 1 1 1V20a1 1 0 0 1-1 1A17 17 0 0 1 3 4a1 1 0 0 1 1-1h3.5a1 1 0 0 1 1 1c0 1.250.2 2.460.57 3.6a1 1 0 0 1-.25 1z"/></svg>
      0400 555 128
    </li>
    <li>
      <svg viewBox="0 0 24 24"><path d="M12 2a10 10 0 1 0 0 20 10 10 0 0 0 0-20zm6.9 6h-2.9a15.7 15.7 0 0 0-1.4-3.6A8 8 0 0 1 18.9 8zM12 4a14 14 0 0 1 1.9 4h-3.8A14 14 0 0 1 12 4zM4.3 14a8 8 0 0 1 0-4h3.4a16.5 16.5 0 0 0 0 4zm.8 2h2.9a15.7 15.7 0 0 0 1.4 3.6A8 8 0 0 1 5.1 16zM8 8H5.1a8 8 0 0 1 4.3-3.6A15.7 15.7 0 0 0 8 8zm4 12a14 14 0 0 1-1.9-4h3.8A14 14 0 0 1 12 20zm2.3-6H9.7a14.7 14.7 0 0 1 0-4h4.6a14.7 14.7 0 0 1 0 4zm.3 5.6a15.7 15.7 0 0 0 1.4-3.6h2.9a8 8 0 0 1-4.3 3.6zm1.7-5.6a16.5 16.5 0 0 0 0-4h3.4a8 8 0 0 1 0 4z"/></svg>
      <span>www.<span class="accent">tmwhomecrafting</span>.com.au</span>
    </li>
    <li>
      <svg viewBox="0 0 24 24"><path d="M3 5h18a1 1 0 0 1 1 1v12a1 1 0 0 1-1 1H3a1 1 0 0 1-1-1V6a1 1 0 0 1 1-1zm1 2.2V17h16V7.2l-8 5.3z"/></svg>
      <span>info@<span class="accent">tmwhomecrafting</span>.com.au</span>
    </li>
  </ul>

  <p class="location">Ashford Vale, Tasmania, Australia</p>
</section>

</body>
</html>
```